Family business needs stationery redesign with new logo

Family owned company, established in 1987 wanting a brand 'refresh'. We are an electrical, refrigeration and construction company based in the Barkly Region Northern Territory, Australia. We have a new logo we would like to use which is uploaded along with our current letterhead and email signature. We are also dropping the word 'contractors' so please do not include this on any designs. Please note also, the 'orange' color used in our logo and designs should be Northern Territory red ochre which is as follows:

RGB (Hex): #C75B12
PantoneĀ® 159 C
CMYK: 1 / 74 / 100 / 7

We are needing our stationery redesigned using our new logo. Please include letterheads, business cards, envelopes, and email signatures.

We currently use our business letterheads for quotations, invoices, letters, HR matters, and internal memos.

We also need a separate simplified letterhead for internal paperwork such as employee leave forms, meeting agendas, and meeting minutes etc.

Reason: Needing more submissions of full package designs. We are wanting all our stationery, including business cards, letterheads, email signatures, envelopes, etc to be cohesive. We also require ALL the information, as supplied on our template letterhead, to be included on the new letterhead designs. including electrical license no.etc Thank you, R&W

Reason: needing more time as work has got in the way of looking over designs. A lot of designs not meeting the brief/criteria.

Industry/Entity Type

Business

Colors
0355a3
f37122

Requirements
Must have
• The 'orange' color used in the designs should be Northern Territory red ochre which is as follows:
• RGB (Hex): #C75B12
• PantoneĀ® 159 C
• CMYK: 1 / 74 / 100 / 7
• ***MUST INCLUDE ALL INFORMATION THAT IS ON OUR CURRENT LETTERHEAD***
Should not have
• Please do not include the word 'contractors'

```html
<!DOCTYPE html>
<html lang="en">
<head>
<meta charset="utf-8">
<title>R&amp;W Business Cards</title>
<link href="https://fonts.googleapis.com/css2?family=Source+Sans+3:wght@400;600;700&display=swap" rel="stylesheet">
<style>
  :root {
    --navy: #1b3170;
    --ochre: #c75b12;
    --white: #ffffff;
    --ink: #4a4a4a;
    --rule: #9a9a9a;
    --backdrop: #e4e4e4;
  }
  html, body {
    margin: 0;
    padding: 0;
    width: 1200px;
    height: 856px;
    overflow: hidden;
    background: var(--backdrop);
    font-family: "Source Sans 3", "Helvetica Neue", Arial, sans-serif;
  }
  .canvas {
    position: relative;
    width: 1200px;
    height: 856px;
  }
  .card {
    position: absolute;
    width: 534px;
    height: 305px;
    border-radius: 16px;
    overflow: hidden;
  }
  .card--front {
    left: 335px;
    top: 113px;
    background: var(--white);
  }
  .card--back {
    top: 438px;
    background: var(--navy);
  }
  .card--back-white { left: 57px; }
  .card--back-ochre { left: 613px; }

  .wordmark {
    position: absolute;
    font-weight: 700;
    line-height: 1;
    white-space: nowrap;
    transform: translate(-50%, -50%);
    letter-spacing: 1px;
  }
  .card--front .wordmark {
    left: 137px;
    top: 148px;
    font-size: 46px;
    color: var(--navy);
  }
  .card--back .wordmark {
    left: 269px;
    top: 144px;
    font-size: 76px;
    color: var(--white);
  }

  .divider {
    position: absolute;
    left: 266px;
    top: 60px;
    width: 1px;
    height: 201px;
    background: var(--rule);
  }
  .contact {
    position: absolute;
    left: 302px;
    top: 66px;
    color: var(--ink);
  }
  .contact__name {
    margin: 0;
    font-size: 19px;
    font-weight: 600;
    color: var(--navy);
    line-height: 1.1;
  }
  .contact__role {
    margin: 2px 0 0;
    font-size: 15px;
    color: var(--ochre);
    line-height: 1.2;
  }
  .contact__address {
    margin: 9px 0 0;
    font-size: 14px;
    line-height: 20px;
    font-style: normal;
  }
  .contact__list {
    list-style: none;
    margin: 6px 0 0;
    padding: 0;
    font-size: 14px;
    line-height: 20px;
  }
  .contact__list li {
    display: flex;
    align-items: center;
    gap: 7px;
  }
  .contact__list svg {
    width: 13px;
    height: 13px;
    fill: var(--navy);
    flex: none;
  }

  .established {
    position: absolute;
    left: 0;
    right: 0;
    top: 248px;
    text-align: center;
    font-size: 20px;
    letter-spacing: 0.5px;
  }
  .established--white { color: var(--white); }
  .established--ochre { color: var(--ochre); }
</style>
</head>
<body>
<main class="canvas">

  <section class="card card--front" aria-label="Business card front">
    <div class="wordmark">R&amp;W</div>
    <div class="divider"></div>
    <div class="contact">
      <p class="contact__name">Dana Hollis</p>
      <p class="contact__role">CEO/Founder</p>
      <address class="contact__address">412 Ridgeline Road<br>Tennant Creek, NT 0860</address>
      <ul class="contact__list">
        <li>
          <svg viewBox="0 0 16 16" aria-hidden="true"><path d="M3.6 1.2l2.3 2.6c.4.4.4 1 0 1.4L4.7 6.5c.9 1.9 2.9 3.9 4.8 4.8l1.3-1.2c.4-.4 1-.4 1.4 0l2.6 2.3c.4.4.4 1 0 1.4l-1.3 1.3c-.6.6-1.6.8-2.4.4C6.5 13.7 2.3 9.5.5 4.9.1 4.1.3 3.1.9 2.5L2.2 1.2c.4-.4 1-.4 1.4 0z"/></svg>
          <span>555 210 4862</span>
        </li>
        <li>
          <svg viewBox="0 0 16 16" aria-hidden="true"><path d="M4 1h8v4H4z"/><path d="M1 6h14v6h-2v-2H3v2H1z"/><path d="M4 11h8v4H4z"/></svg>
          <span>555 210 4863</span>
        </li>
        <li>
          <svg viewBox="0 0 16 16" aria-hidden="true"><path d="M1 3h14v10H1z" opacity=".0"/><path d="M1 3h14v1.2L8 9 1 4.2z"/><path d="M1 5.6l7 4.8 7-4.8V13H1z"/></svg>
          <span>office@rwsite.com</span>
        </li>
        <li>
          <svg viewBox="0 0 16 16" aria-hidden="true"><path d="M8 1a7 7 0 100 14A7 7 0 008 1zm0 1.5c.6 0 1.5 1.3 1.9 3.5H6.1C6.5 3.8 7.4 2.5 8 2.5zM5 4.1c-.2.6-.4 1.2-.5 1.9H2.9A5.5 5.5 0 015 4.1zM2.6 7.5h1.8a12 12 0 000 1H2.6a5.6 5.6 0 010-1zm.3 2.5h1.6c.1.7.3 1.3.5 1.9A5.5 5.5 0 012.9 10zM8 13.5c-.6 0-1.5-1.3-1.9-3.5h3.8c-.4 2.2-1.3 3.5-1.9 3.5zm-2-5a10 10 0 010-1h4a10 10 0 010 1zm5 3.4c.2-.6.4-1.2.5-1.9h1.6a5.5 5.5 0 01-2.1 1.9zm.6-3.4a12 12 0 000-1h1.8a5.6 5.6 0 010 1zM11.5 6c-.1-.7-.3-1.3-.5-1.9A5.5 5.5 0 0113.1 6z"/></svg>
          <span>www.rwsite.com</span>
        </li>
      </ul>
    </div>
  </section>

  <section class="card card--back card--back-white" aria-label="Business card back, white variant">
    <div class="wordmark">R&amp;W</div>
    <p class="established established--white">Est. 1987</p>
  </section>

  <section class="card card--back card--back-ochre" aria-label="Business card back, ochre variant">
    <div class="wordmark">R&amp;W</div>
    <p class="established established--ochre">Est. 1987</p>
  </section>

</main>
</body>
</html>
```